A gateway to the eyes of potential Talquen Candidates and Clients

We are looking for a brochure that will grab attention, all most along the lines of an infogram. The business supplies people to the construction sector. So we want it simple but sharp.

I would like the brochure to be able to have a half fold effect when printed but the main focus will be to use it in an e-brochure format.

Main pages will be as follows:

About Us: Which will have a bit about the management team and some pictures.

Services: information for both candidate and clients.

Why us?:

Contact: Location, contact numbers etc.

FOR CONTENTS:
website will give you the content required. www.talquenbuilders.co.uk
Updates

Project Deadline Extended Reason: Project was moved from a flyer to a brochure and the logo didn't upload. So I will be uploading my new logo and it will give additional time to get designs in. Cheers Added Monday, June 20, 2016

Target Market(s)

Clients and candidates for the construction market

Industry/Entity Type

Business

Requirements
Must have
• Bold and strong images of the construction sector. A simple to read format. Also needs to look good in an electronic format.
Nice to have
• I like the idea of a black and white model but with certain parts of the images highlighted in our colours.
Should not have
• Too much of a complex lay out.

```html
<!DOCTYPE html>
<html lang="en">
<head>
<meta charset="utf-8">
<title>Talquen Construction – Brochure Cover</title>
<link href="https://fonts.googleapis.com/css2?family=Open+Sans:wght@400;600;700&family=Questrial&display=swap" rel="stylesheet">
<style>
  :root {
    --page-bg: #ece9e4;
    --paper: #ffffff;
    --ink: #3a3a3a;
    --ink-soft: #555b62;
    --brand-blue: #1a8bd0;
    --brand-blue-deep: #1479bd;
    --brand-orange: #f08a0c;
    --brand-amber: #f3b01a;
    --sky-top: #4f8fd6;
    --sky-low: #a9c6e6;
    --concrete: #b9b5ae;
  }
  * { margin: 0; padding: 0; box-sizing: border-box; }
  html, body {
    width: 1200px; height: 804px; overflow: hidden;
    background: var(--page-bg);
  }
  .cover {
    position: absolute; left: 331px; top: 22px;
    width: 538px; height: 760px;
    background: var(--paper);
    box-shadow: 0 6px 22px rgba(0,0,0,.18);
    font-family: "Open Sans", Arial, sans-serif;
    overflow: hidden;
  }
  .tagline {
    position: absolute; left: 30px; top: 64px;
    font-size: 15px; color: var(--ink); letter-spacing: .2px;
  }
  .brand {
    position: absolute; right: 36px; top: 30px;
    display: flex; align-items: center; gap: 7px;
  }
  .brand-mark {
    width: 16px; height: 16px; background: var(--brand-blue);
  }
  .brand-name {
    font-family: "Questrial", sans-serif;
    font-size: 19px; color: var(--brand-orange); letter-spacing: 1px;
  }
  .hero-photo {
    position: absolute; left: 22px; right: 0; top: 102px; height: 360px;
    background:
      linear-gradient(180deg, transparent 55%, rgba(185,181,174,.55) 80%, var(--concrete) 100%),
      linear-gradient(200deg, var(--sky-top) 0%, #6fa3dc 45%, var(--sky-low) 100%);
  }
  .feature-band {
    position: absolute; left: 22px; right: 0; top: 462px; height: 178px;
    display: flex;
  }
  .quote-panel {
    width: 38%;
    background: linear-gradient(90deg, var(--brand-amber) 0%, var(--brand-orange) 100%);
    position: relative;
  }
  .quote-icon {
    position: absolute; left: 24px; top: 86px;
  }
  .quote-text {
    position: absolute; left: 56px; top: 76px; right: 10px;
    font-size: 10.5px; font-weight: 600; line-height: 1.2; color: #fff;
  }
  .quote-author {
    font-size: 6px; font-weight: 400; margin-left: 4px; text-transform: uppercase;
  }
  .intro-panel {
    flex: 1;
    background: linear-gradient(180deg, var(--brand-blue) 0%, var(--brand-blue-deep) 100%);
    padding: 52px 26px 0 30px;
    color: #fff;
  }
  .intro-title {
    font-family: "Questrial", sans-serif; font-weight: 400;
    font-size: 27px; letter-spacing: .5px; margin-bottom: 22px;
  }
  .intro-copy {
    font-size: 9.5px; line-height: 1.55;
  }
  .site-address {
    position: absolute; left: 0; right: 0; top: 690px;
    text-align: center; font-size: 11px; letter-spacing: 1.6px; color: var(--ink-soft);
  }
</style>
</head>
<body>
  <article class="cover">
    <p class="tagline">Be a better version of you...</p>

    <div class="brand">
      <span class="brand-mark"></span>
      <span class="brand-name">TALQUEN</span>
    </div>

    <div class="hero-photo" role="img" aria-label="Photograph of tower cranes over a concrete high-rise under construction against a blue sky"></div>

    <section class="feature-band">
      <div class="quote-panel">
        <svg class="quote-icon" width="24" height="24" viewBox="0 0 24 24" aria-hidden="true">
          <rect x="0" y="0" width="24" height="24" fill="#ffffff"/>
          <rect x="0" y="0" width="13" height="13" fill="#3a3a3a"/>
          <rect x="13" y="13" width="11" height="11" fill="#d9d9d9"/>
        </svg>
        <p class="quote-text">“Your life does not get better by chance, it gets better by change”<span class="quote-author">Dale Morrow</span></p>
      </div>
      <div class="intro-panel">
        <h1 class="intro-title">TALQUEN Construction</h1>
        <p class="intro-copy">Fresh start? New Job? Brighter Future? A Better you? Talquen Construction is in your corner.</p>
      </div>
    </section>

    <p class="site-address">www.talquenbuilders.co.uk</p>
  </article>
</body>
</html>
```